Coffee and Plastics

I am looking for a completely new site that shows the products we have. Our current site is www.velmorebrothersbeans.com. We are open minded to what designers come up with. Our current site is www.velmorebrothersbeans.com. You can you the information from there to start the site. I need these tabs on the main home page. ( Home, Coffee & Tea, Condiments, and Paper and Plastics, and Contact.) You can take photos and info from my Current site. In products page.
I will be uploading info and photo for paper and plastics.
Look and feel
Each slider illustrates characteristics of the customer's brand and the style your logo design should communicate.

```html
<!DOCTYPE html>
<html lang="en">
<head>
<meta charset="utf-8">
<title>Velmore Brothers Beans</title>
<link rel="stylesheet" href="https://fonts.googleapis.com/css2?family=Sofia&family=Cabin:wght@400;500&display=swap">
<style>
:root{
  --rust:#b4553a;
  --rust-dark:#9c4630;
  --bg-dark:#2b221d;
  --ink:#3a2f2a;
  --muted:#8a817c;
  --card:#f4f1ef;
  --white:#ffffff;
  --cream:#f6e8df;
}
*{box-sizing:border-box;margin:0;padding:0}
html,body{width:709px;height:1200px;overflow:hidden}
body{background:var(--bg-dark);font-family:"Cabin",Arial,sans-serif;color:var(--ink)}
.page{position:relative;width:709px;height:1200px;overflow:hidden;
  background:radial-gradient(ellipse at 95% 10%,#5a4334 0%,#3a2d25 30%,var(--bg-dark) 65%)}
.bean-bg{position:absolute;right:0;top:0;width:230px;height:360px;
  background:radial-gradient(ellipse at 70% 25%,rgba(120,85,60,.55),rgba(43,34,29,0) 70%)}
.brand-name{position:absolute;left:75px;top:22px;font-family:"Sofia",cursive;font-size:29px;color:var(--white)}
.hours{position:absolute;right:77px;top:32px;text-align:right;font-size:8.5px;line-height:12.5px;color:var(--white)}
.frame{position:absolute;left:78px;top:80px;width:553px;height:1092px;background:var(--rust)}
.nav{position:absolute;left:0;top:0;width:553px;height:36px;display:flex;align-items:center;padding-left:13px}
.nav a{color:var(--white);text-decoration:none;font-size:11px;margin-right:28px}
.nav a.active{color:var(--ink)}
.search{position:absolute;right:6px;top:5px;width:28px;height:24px;background:var(--rust-dark);border:1px solid #c86b50}
.sheet{position:absolute;left:5px;top:36px;width:543px;height:894px;background:var(--white);overflow:hidden}
.hero{position:absolute;left:0;top:0;width:543px;height:262px;
  background:linear-gradient(110deg,#fbfbfb 0%,#f2f0ee 45%,#d9cfc8 60%,#8a5a3a 75%,#5a3522 100%)}
.hero-h1{position:absolute;left:22px;top:92px;font-family:"Sofia",cursive;font-size:33px;color:#222}
.hero-h2{position:absolute;left:22px;top:140px;font-family:"Sofia",cursive;font-size:24px;color:var(--rust)}
.dots{position:absolute;left:254px;top:276px;display:flex;gap:3px}
.dots i{width:5px;height:5px;border-radius:50%;background:#aaa}
.dots i.on{background:var(--rust)}
.title{position:absolute;left:0;width:543px;height:30px;line-height:30px;text-align:center;font-family:"Sofia",cursive;font-size:18px;font-weight:400;color:var(--ink);white-space:nowrap}
.title b{color:var(--rust);font-weight:400;font-size:26px;vertical-align:-3px;margin:0 6px}
.arrow{display:inline-block;width:15px;height:15px;border-radius:50%;vertical-align:-2px;margin:0 8px;position:relative}
.arrow.prev{background:#b9b9b9}.arrow.next{background:var(--rust)}
.arrow::after{content:"";position:absolute;top:5px;width:5px;height:5px;border:solid var(--white);border-width:0 0 1.5px 1.5px}
.arrow.prev::after{left:6px;transform:rotate(45deg)}
.arrow.next::after{left:4px;transform:rotate(-135deg)}
.intro{position:absolute;left:42px;top:341px;width:460px;text-align:center;font-size:8.3px;line-height:14px;color:#555}
.btn{position:absolute;left:213px;top:391px;width:116px;height:27px;background:var(--rust);color:var(--white);font-size:8.5px;text-align:center;line-height:27px}
.products{position:absolute;left:0;top:440px;width:543px;height:250px;background:linear-gradient(#f5f5f5,#fff 30%,#fff 85%,#f1f1f1)}
.card{position:absolute;top:54px;width:122px;height:159px;background:var(--card);border:1px solid #ddd}
.card .ph{height:77px;border:2px solid #7c6a60}
.card h3{font-size:8px;font-weight:500;margin:8px 0 0 8px;color:#222}
.card p{font-family:Arial,sans-serif;font-size:6.3px;line-height:10px;color:#888;margin:6px 8px 0 9px}
.card hr{border:0;border-top:1px solid #ddd;margin:8px 8px 0}
.card a{display:block;font-family:Arial,sans-serif;font-size:6.5px;color:var(--rust);margin:6px 0 0 10px;text-decoration:none}
.brands{position:absolute;left:0;top:690px;width:543px;height:204px}
.tagline{position:absolute;left:0;top:61px;width:543px;text-align:center;font-size:10.5px;color:var(--rust)}
.badges{position:absolute;left:10px;width:525px;display:flex;justify-content:space-between}
.badges i{display:block;height:40px;border-radius:4px}
.footer{position:absolute;left:0;top:930px;width:553px;height:162px}
.col{position:absolute;top:12px;color:var(--white);font-size:7px;line-height:12.2px}
.col h4{font-family:"Sofia",cursive;font-weight:400;font-size:15px;color:var(--cream);margin-bottom:3px}
.social{display:flex;gap:5px;margin-top:7px}
.social i{width:10px;height:10px;border-radius:50%;background:var(--cream)}
.rule{position:absolute;left:17px;top:121px;width:518px;height:1px;background:#c6735a}
.credit{position:absolute;left:0;top:138px;width:553px;text-align:center;font-family:Arial,sans-serif;font-size:6.5px;color:var(--white)}
.code{position:absolute;left:660px;top:1137px;font-family:Arial,sans-serif;font-size:7px;color:var(--white)}
</style>
</head>
<body>
<div class="page">
  <div class="bean-bg" role="img" aria-label="Roasted coffee beans in the background"></div>
  <div class="brand-name">Velmore Brothers Beans</div>
  <div class="hours">1-800-555-0142<br>Mon - fri 9- 5 Central Time</div>

  <div class="frame">
    <nav class="nav">
      <a class="active">Home</a><a>Coffee &amp; Tea</a><a>Condiments</a><a>Paper</a><a>Plastics</a><a>Contact</a>
      <div class="search">
        <svg width="28" height="24" viewBox="0 0 28 24"><circle cx="12" cy="10" r="3.5" fill="none" stroke="#fff" stroke-width="1.6"/><line x1="14.5" y1="12.5" x2="18" y2="16" stroke="#fff" stroke-width="2"/></svg>
      </div>
    </nav>

    <main class="sheet">
      <div class="hero" role="img" aria-label="Coffee pouring into a white cup on a saucer with coffee beans"></div>
      <div class="hero-h1">At once you</div>
      <div class="hero-h2">Will notice that we were</div>
      <div class="dots"><i></i><i></i><i class="on"></i><i></i><i></i></div>

      <h2 class="title" style="top:295px"><b>{</b>Welcome To Velmore Brothers Beans<b>}</b></h2>
      <p class="intro">We are a family-owned and operated business based in Marlow Texas. Since the opening of Velmore Brothers Beans plant in 1995, we have become Texas' premier independently owned coffee packaging company. Our success relies solely on the principle of selling only the freshest, highest-quality in-room coffee available.</p>
      <div class="btn">Read More Info</div>

      <section class="products">
        <h2 class="title" style="top:11px"><span class="arrow prev"></span><b>{</b>Our Products<b>}</b><span class="arrow next"></span></h2>
        <div class="card" style="left:7px"><div class="ph" role="img" aria-label="Paper coffee cup with white lid" style="background:linear-gradient(90deg,#e8e6e3 45%,#c9a27e 55%,#8a6a4d)"></div><h3>Neque porro quisquam est</h3><p>Lorem Ipsum is simply dummy text of the printing and typeset ting industry.</p><hr><a>Read More ›</a></div>
        <div class="card" style="left:141px"><div class="ph" role="img" aria-label="Gold plastic compartment tray" style="background:linear-gradient(135deg,#d8b86a,#a98530)"></div><h3>Neque porro quisquam est</h3><p>Lorem Ipsum is simply dummy text of the printing and typeset ting industry.</p><hr><a>Read More ›</a></div>
        <div class="card" style="left:278px"><div class="ph" role="img" aria-label="Round gold plastic serving tray" style="background:radial-gradient(circle,#e0c27a,#8f6d2a)"></div><h3>Neque porro quisquam est</h3><p>Lorem Ipsum is simply dummy text of the printing and typeset ting industry.</p><hr><a>Read More ›</a></div>
        <div class="card" style="left:412px"><div class="ph" role="img" aria-label="White plastic cup" style="background:radial-gradient(circle,#ffffff,#dcdcdc)"></div><h3>Neque porro quisquam est</h3><p>Lorem Ipsum is simply dummy text of the printing and typeset ting industry.</p><hr><a>Read More ›</a></div>
      </section>

      <section class="brands">
        <h2 class="title" style="top:13px"><span class="arrow prev"></span><b>{</b>Our Brands<b>}</b><span class="arrow next"></span></h2>
        <p class="tagline">We guarantee all of our products will meet your level of satisfaction.</p>
        <div class="badges" style="top:84px">
          <i style="width:62px;background:#3a6fc4"></i><i style="width:58px;background:#2e3f8a"></i><i style="width:56px;background:#1d3f7a"></i><i style="width:58px;background:#5a2a22"></i><i style="width:56px;background:#1f8a55"></i><i style="width:60px;background:#23357a"></i><i style="width:40px;background:#1f5a3a"></i><i style="width:56px;background:#243a9a"></i>
        </div>
        <div class="badges" style="top:134px">
          <i style="width:66px;background:#e9e9e9"></i><i style="width:40px;background:#1f4e9a"></i><i style="width:48px;background:#1a2d7a"></i><i style="width:54px;background:#2a7a4a"></i><i style="width:40px;background:#c42a2a"></i><i style="width:46px;background:#2a3a8a"></i><i style="width:94px;background:#eadede"></i><i style="width:56px;background:#e6e6e6"></i>
        </div>
      </section>
    </main>

    <footer class="footer">
      <div class="col" style="left:17px"><h4>Information</h4>Home,<br>Coffee &amp; Tea,<br>Condiments,<br>Paper,<br>Plastics,<br>Contact</div>
      <div class="col" style="left:130px"><h4>Services</h4>Online Shopping<br>Orders and Returns<br>discount offer<br>investor relations<br>corporate responsibility</div>
      <div class="col" style="left:276px"><h4>Customer Care</h4>Contact Us<br>Shipping<br>Returns &amp; Exchanges<br>Payment &amp; Insurance<br>investor relations</div>
      <div class="col" style="left:412px"><h4>Contact us</h4>Velmore Brothers Beans<br>418 Cedar Mill Road<br>Tel 0123-555-0178<br>Email sales@velmorebeans.com
        <div class="social"><i></i><i></i><i></i><i></i></div></div>
      <div class="rule"></div>
      <div class="credit">All rights reserved. Login</div>
    </footer>
  </div>
  <div class="code">C4</div>
</div>
</body>
</html>
```